Classy, Elegant, Simple Business Card Design

Looking to have a classy, simple, and elegant design. Want a top notch designed business card. I really like the look of the new torvane credit card. I also like the design I attached. I am trying to reach 21-29 year old females for booking us for there wedding or event. We offer Disc Jockey Service, Photo Booth Rentals, and Uplighting .

Target Market(s)

21-28 year old females

Contact Information for Business Card

Has to have logo, website, email, and phone number

Font styles to use
Other font styles liked:
• open to font choice, modern, clean
Designer to choose
33a6d7
0791cd
0555a3
ffffff

Requirements
Must have
• Has to have logo, website, email, and phone number
Nice to have
• I really like the design of the new torvane credit card. I also included my logo and some designs I like
Should not have
• clutter or too much info

```html
<!DOCTYPE html>
<html lang="en">
<head>
<meta charset="utf-8">
<title>Velvetline Event Group – Business Card</title>
<link href="https://fonts.googleapis.com/css2?family=Jost:wght@400;500&family=Roboto:wght@400;700&display=swap" rel="stylesheet">
<style>
  :root {
    --stage: #3b3b3d;
    --card: #1d1e21;
    --silver: #a9abb0;
    --white: #ffffff;
    --blue-light: #33a6d7;
    --blue: #0791cd;
    --blue-deep: #0555a3;
  }
  * { box-sizing: border-box; margin: 0; padding: 0; }
  html, body { width: 799px; height: 1200px; overflow: hidden; }
  body {
    background: var(--stage);
    position: relative;
    font-family: "Roboto", sans-serif;
  }
  .card {
    position: absolute;
    left: 80px;
    width: 640px;
    height: 366px;
    background: var(--card);
    border-radius: 4px;
    box-shadow: 0 10px 30px rgba(0,0,0,0.45);
    overflow: hidden;
  }
  .card--front { top: 110px; }
  .card--back { top: 724px; }

  .front-brand {
    position: absolute;
    inset: 0;
    display: flex;
    flex-direction: column;
    align-items: center;
    justify-content: center;
    text-align: center;
  }
  .brand-name {
    font-family: "Jost", sans-serif;
    font-weight: 400;
    color: var(--silver);
    font-size: 46px;
    letter-spacing: 3px;
    text-transform: uppercase;
    line-height: 1.1;
  }
  .brand-name--small {
    font-size: 22px;
    letter-spacing: 2px;
    color: var(--white);
  }

  .back-brand {
    position: absolute;
    left: 40px;
    top: 38px;
  }
  .contact {
    position: absolute;
    left: 40px;
    top: 140px;
  }
  .person-name {
    color: var(--blue);
    font-weight: 700;
    font-size: 26px;
  }
  .person-role {
    color: var(--white);
    font-size: 16px;
    margin-top: 4px;
  }
  .contact-list {
    list-style: none;
    margin-top: 26px;
  }
  .contact-list li {
    display: flex;
    align-items: center;
    gap: 12px;
    color: var(--white);
    font-size: 16px;
    margin-bottom: 9px;
  }
  .contact-list svg { width: 15px; height: 15px; flex: none; }

  .back-mark {
    position: absolute;
    right: 70px;
    top: 73px;
    width: 220px;
    height: 220px;
    border-radius: 50%;
    background: linear-gradient(160deg, var(--blue-light), var(--blue) 55%, var(--blue-deep));
  }
</style>
</head>
<body>
  <section class="card card--front">
    <div class="front-brand">
      <p class="brand-name">Velvetline Event Group</p>
    </div>
  </section>

  <section class="card card--back">
    <div class="back-brand">
      <p class="brand-name brand-name--small">Velvetline Event Group</p>
    </div>

    <div class="contact">
      <p class="person-name">Marcus Hale</p>
      <p class="person-role">Founder &amp; CEO</p>
      <ul class="contact-list">
        <li>
          <svg viewBox="0 0 16 16" aria-hidden="true"><path fill="#0791cd" d="M3.5 1.5l2.6 0 1 3.4-1.6 1.2a8 8 0 0 0 4.4 4.4l1.2-1.6 3.4 1v2.6c0 .8-.7 1.5-1.5 1.5A12.5 12.5 0 0 1 2 3c0-.8.7-1.5 1.5-1.5z"/></svg>
          612 4418 2760
        </li>
        <li>
          <svg viewBox="0 0 16 16" aria-hidden="true"><rect x="1" y="3" width="14" height="10" rx="1" fill="#0791cd"/><polyline points="1.5,3.8 8,9 14.5,3.8" fill="none" stroke="#1d1e21" stroke-width="1.3"/></svg>
          marcus@velvetline.com
        </li>
        <li>
          <svg viewBox="0 0 16 16" aria-hidden="true"><g fill="none" stroke="#0791cd" stroke-width="1.4"><circle cx="8" cy="8" r="6.5"/><ellipse cx="8" cy="8" rx="2.8" ry="6.5"/><line x1="1.5" y1="8" x2="14.5" y2="8"/></g></svg>
          www.velvetline.com
        </li>
      </ul>
    </div>

    <div class="back-mark" aria-hidden="true"></div>
  </section>
</body>
</html>
```